Edgey, Modern Air Conditioning Website

Bramble Works
current website - www.kelvaroom.nz
Facebook - www.facebook.com/bramwrk

We really have no idea about webdesign etc we are Engineers not Graphic artists or creative writers. We really just want a edgy, modern website completed on our behalf

We can get pictures of projects as directed or happy for you to use stock images of Talvoro Mecha NZ (Heatpumps) air conditioning and exposed ducting etc

we would like the website to be heavily based on the below website. I like what they have done with both the site and the app but obviously would need to suit Bramble Works, snowflakes heating cooling etc etc Blue and white to match our logo etc

http://parrowbeams.co.nz/

Need links to contact page:
Bramble Works
27 Harlow Crescent
Petone
Wellington

0800 529 174 (0800BRAMWKS)

Marta.k@bramwks.co.nz

BRAMBLE WORKS
SATISFACTION GAURANTEED

WHY CHOOSE BRAMBLE WORKS
EXPERIENCE COUNTS

We have a team of nationally trained and qualified Refrigeration/HVAC/Electrical Engineers and Technicians based in Petone, Wellington offering services to Wellington, Manuwatu and the Wairarapa. We are factory trained and authorised to design, service and install all major brands including Talvoro, Pelnor, Korrowane Electric, Veltrada and Osmelo units. We extend our installation warranty to match that of the manufacturer’s warranty and specialise in our own diagnostics and repair.

SATISFACTION GUARANTEE
We aim to please and I put my name behind our brand! We will take care of your project from start to finish and offer a unique experience with our 100% satisfaction Guarantee*. We will supply and install your system and if your system is not installed how it was explained or not up to a trades standard we will return to make any the necessary modifications free of charge. We back this service up with our 0% upfront strategy, the power is in your hands. We will only invoice you once the installation has been completed up to a BRAMBLE WORKS standard.

LOW PRESSURE SALES
Nobody likes the vacuum salesmen’s techniques and neither do we. We will come to your home or business to provide a free measure and quote. Our experience will insure this is a quick and painless experience, you will be provided with expert advice from a qualified Refrigeration Engineer, not a car salesmen turned “Heating Guru”. We will follow up with an email providing our best price straight up, installation details and online brochures. We won’t bug you with repeated phone calls and inbox clogging emails. Once we receive confirmation we will issue you with an installation date and typically have your installation completed within 10 working days.

BRANDS
www.talvoromecha.co.nz
www.pelnor.co.nz
http://quellaro.co.nz/

SERVICES
Heatpumps/Air Conditioning – Heat pumps are the most efficient way of using electricity to heat your home, but some are more efficient than others. We will select the right model for your requirements taking into account the capacity required, the visual impact of the system, the style of system, air flow and obviously your personal preferences. We only install the highest quality brands that offer outstanding after sales support. Cassettes, Consoles, Under Ceilings, Ducted, Hiwalls, Multis… Confused? Give us a call.

COMMERCIAL
We have a growing Portfolio of clients that rely on us for their Commercial requirements. We have proven ourselves to be a force to be reckoned with to be able to think outside the square and come up with unique and cost effective solutions to heat and cool large areas.

CENTRAL HEATING
Ducted Heatpumps are the holy grail of central heating and guess what? They can also cool and dehumidify your home. Ducted Heatpumps are often overlooked or priced out of reach by less experienced salesmen as its not just a point and shoot approach. We pride ourselves in our work with Ducted systems, we are able to provide quick and economic quotations and can provide expert advice on all the extra options on Ducted systems with zone control, fresh air integration, positive pressure solutions. We use the best materials when it comes to insulated ducting, mounting equipment, drainage materials. Every system we design is designed with the lowest possible decibel reading, least amount of static pressure and maximum effieciency with the help of the very latest software available.

VENTILATION
Home ventilation is a very important part of insuring you have a nice dry home to maximise the efficiency of your Heat pump. Whilst HRV systems are not designed to Heat your house they are designed to keep it dry, provide fresh filtered air to ensure your home healthy and easy to heat. We offer a number of solutions from integrated ducted heatpump systems to balanced heat recovery systems and positive air systems.

TESTIMONIALS
http://www.lotbazaro.co.nz/Browse/Listing.aspx?id=415728306

Target Market(s)

Home Owners

Industry/Entity Type

Air Conditioning

Colors
33a6d7
ffffff

Requirements
Must have
• Could possibly use the 'O' from Bramble Works logo throughout website - see business Card
Nice to have
• Bright & Crisp - White and Blue
• Would love to have our Logo used throughout the website.

```html
<!DOCTYPE html>
<html lang="en">
<head>
<meta charset="utf-8">
<title>Bramble Works – Commercial &amp; Central Heating</title>
<link rel="stylesheet" href="https://fonts.googleapis.com/css2?family=Raleway:wght@300;400;500;600;700&family=Lato:wght@400;700&display=swap">
<style>
:root{
  --blue:#33a6d7;
  --blue-deep:#1e8fc2;
  --orange:#f5a417;
  --ink:#333;
  --muted:#666;
  --light:#f1f1f1;
  --white:#fff;
  --black:#050505;
}
*{box-sizing:border-box;margin:0;padding:0}
html,body{width:1200px;height:3120px;overflow:hidden}
body{font-family:'Lato',sans-serif;color:var(--ink);background:var(--white);position:relative}
section,header,footer,.topbar,.bottombar{position:relative;width:1200px;overflow:hidden}
.abs{position:absolute}
.h-title{font-family:'Raleway',sans-serif;font-weight:400;font-size:28px;letter-spacing:.5px;display:flex;align-items:center;gap:12px;color:#222;white-space:nowrap}
.h-title b{font-weight:700;color:var(--blue)}
.ring{width:30px;height:30px;border-radius:50%;border:4px dotted #888;flex:none}
.btn{display:inline-block;font-family:'Lato',sans-serif;font-size:14px;color:var(--white);padding:0 16px;height:36px;line-height:36px;border-radius:2px;white-space:nowrap}
.btn-blue{background:var(--blue)}
.btn-orange{background:var(--orange)}

/* top bar */
.topbar{height:34px;background:var(--blue);color:var(--white);font-size:12px}
.topbar .addr{left:162px;top:10px;display:flex;gap:8px;align-items:center}
.social{right:162px;top:0;display:flex}
.social span{width:30px;height:34px;display:flex;align-items:center;justify-content:center}
.social span:nth-child(odd){background:var(--blue-deep)}
.social i{width:10px;height:10px;background:var(--white);border-radius:50%;display:block}

/* header */
header{height:91px;background:var(--white)}
.brand{left:162px;top:30px;font-family:'Raleway',sans-serif;font-weight:700;font-size:20px;color:var(--blue);display:flex;align-items:center;gap:8px;line-height:1;white-space:nowrap}
.brand .dot{width:16px;height:16px;border-radius:50%;background:var(--blue)}
.nav{left:389px;top:36px;display:flex;gap:33px;font-family:'Raleway',sans-serif;font-size:12px;font-weight:500;color:#333;white-space:nowrap}
.nav .on{color:var(--blue)}
.callus{right:162px;top:22px;text-align:right;font-size:15px;color:#555}
.callus .num{font-family:'Raleway',sans-serif;font-size:21px;color:var(--blue);display:flex;align-items:center;gap:8px;justify-content:flex-end}

/* hero */
.hero{height:491px;background:linear-gradient(100deg,#3c3f44 0%,#6d7075 45%,#8a8c8f 70%,#5c5f63 100%)}
.hero-photo{inset:0}
.hero-shade{inset:0;background:linear-gradient(90deg,rgba(0,0,0,.35),rgba(0,0,0,0) 60%)}
.hero-copy{left:162px;top:160px;color:var(--white)}
.hero-copy h1{font-family:'Raleway',sans-serif;font-weight:700;font-size:35px;letter-spacing:1px}
.hero-copy p{font-family:'Raleway',sans-serif;font-weight:300;font-size:27px;line-height:33px;margin-top:8px}
.hero-copy .btns{margin-top:16px;display:flex;gap:10px}
.dots{left:576px;top:440px;display:flex;gap:6px;align-items:center}
.dots i{width:12px;height:12px;border-radius:50%;background:var(--blue);display:block}
.dots i.on{width:16px;height:16px;background:var(--orange)}
.hero-stripe{left:0;bottom:0;width:1200px;height:9px;background:var(--blue)}

/* about */
.about{height:412px}
.about .h-title{left:162px;top:40px}
.about .sub{left:162px;top:86px;font-family:'Raleway',sans-serif;font-size:15px;color:var(--blue)}
.about .lead{left:162px;top:120px;width:455px;font-size:11.5px;line-height:16px;color:var(--muted)}
.ticks{left:162px;top:186px;list-style:none;font-size:13px;color:#555}
.ticks li{display:flex;align-items:center;gap:14px;height:24px;white-space:nowrap}
.about .btns{left:162px;top:328px;display:flex;gap:10px}
.about-photo{left:653px;top:45px;width:387px;height:319px;border:5px solid var(--white);box-shadow:0 0 4px rgba(0,0,0,.25);background:linear-gradient(160deg,#e6e4df 0%,#8a7e73 45%,#5a4a42 70%,#c9c1b6 100%)}

/* services */
.services{height:616px;background:var(--blue);color:var(--white)}
.services .h-title{left:0;width:1200px;top:40px;justify-content:center;color:var(--white)}
.services .h-title b{color:var(--white)}
.services .h-title .ring{border-color:rgba(255,255,255,.85)}
.services .intro{left:162px;top:94px;width:876px;font-size:11px;line-height:15px;text-align:center;opacity:.95}
.svc{top:172px;width:242px;height:358px}
.svc svg{position:absolute;inset:0}
.svc h3{position:absolute;top:198px;width:100%;text-align:center;font-family:'Raleway',sans-serif;font-weight:400;font-size:19px;letter-spacing:.5px}
.svc p{position:absolute;top:228px;left:32px;width:178px;text-align:center;font-size:11px;line-height:15.5px}
.svc .btn{position:absolute;top:320px;left:58px;width:126px;text-align:center;height:34px;line-height:34px}
.services .cta{left:0;width:1200px;top:548px;text-align:center;font-family:'Raleway',sans-serif;font-size:21px;letter-spacing:.5px}

/* why choose */
.why{height:359px;background:var(--light)}
.why .h-title{left:0;width:1200px;top:30px;justify-content:center}
.feature{top:100px;width:260px;text-align:center}
.feature .art{width:124px;height:118px;margin:0 auto;border-radius:50%;background:radial-gradient(circle,#e3e3e3 0%,#ececec 70%,transparent 71%);position:relative}
.feature .art i{position:absolute;left:30px;top:26px;width:64px;height:64px;border-radius:10px}
.feature h4{margin-top:26px;font-family:'Raleway',sans-serif;font-weight:700;font-size:14px;line-height:17px;color:#222;letter-spacing:.5px}
.feature p{margin-top:8px;font-size:11.5px;line-height:16px;color:#555}

/* areas */
.areas{height:254px}
.areas .h-title{left:162px;top:40px}
.areas .loc{left:162px;top:95px;display:flex;gap:12px}
.loc .name{font-family:'Raleway',sans-serif;font-weight:700;font-size:14px;color:var(--orange)}
.loc .street{font-size:14px;color:#555;white-space:nowrap}
.areas .rule{left:162px;top:142px;width:275px;height:1px;background:#ddd}
.areas .list{left:162px;top:152px;width:200px;font-size:12.5px;line-height:17px;color:#555}
.areas-map{left:537px;top:20px;width:503px;height:204px;background:radial-gradient(ellipse at 40% 50%,#f4f4f4 0%,#fbfbfb 60%,#fff 100%)}
.map-tag{left:540px;top:114px;background:var(--blue);color:var(--white);font-size:11px;padding:3px 10px;border-radius:2px}

/* testimonials */
.testimonials{height:333px;background:linear-gradient(180deg,#e9e9e9,#dcdcdc)}
.testimonials .h-title{left:0;width:1200px;top:42px;justify-content:center}
.quote{top:100px;width:275px;height:181px;background:var(--white);box-shadow:0 1px 3px rgba(0,0,0,.12);padding:22px 26px}
.quote p{font-size:12px;line-height:18px;color:#333}
.quote .who{position:absolute;left:26px;top:112px;display:flex;gap:16px;align-items:center}
.avatar{width:60px;height:60px;border-radius:50%;border:3px solid var(--blue);background:linear-gradient(180deg,#c9b8a8,#7a6a60)}
.who b{display:block;font-family:'Raleway',sans-serif;font-size:13px;color:#222}
.who b.hl{color:var(--orange)}
.who span{font-size:11px;color:#666}

/* quick contact */
.contact{height:239px}
.contact .title{left:162px;top:42px;display:flex;gap:12px}
.contact .title .ring{margin-top:4px}
.contact .title div{font-family:'Raleway',sans-serif;font-size:21px;line-height:25px;letter-spacing:1px;color:#222}
.contact .title b{color:var(--blue);font-weight:600}
.contact .blurb{left:162px;top:120px;width:270px;font-size:11.5px;line-height:17px;color:#555}
.contact .ask{left:477px;top:42px;font-size:13px;color:#444}
.field{width:270px;height:34px;border:1px solid #ccc;font-size:11px;color:#999;padding:0 12px;line-height:32px}
.contact .btn{left:477px;top:162px;height:34px;line-height:34px;padding:0 20px}

/* footer */
footer{height:241px;background:var(--black);color:var(--white)}
footer h5{font-family:'Raleway',sans-serif;font-weight:400;font-size:16px;letter-spacing:1px}
footer h5 b{font-weight:700}
.qlinks{left:162px;top:40px}
.qlinks ul{list-style:none;margin-top:16px;font-size:12.5px;line-height:23px}
.qlinks li::before{content:"›";margin-right:12px}
.cinfo{left:378px;top:40px;font-size:12px}
.cinfo .row{display:flex;gap:14px;margin-top:16px;line-height:16px}
.cinfo .row svg{flex:none;margin-top:1px}
.fmap{left:651px;top:45px;width:389px;height:124px;border-radius:3px;background:linear-gradient(135deg,#e7e4dc 0%,#d8e4cf 50%,#cfe1f2 100%)}
.fmap-link{left:651px;top:178px;font-size:12px;color:#999}
.bottombar{height:50px;background:var(--blue);color:var(--white);font-size:12px}
.follow{left:162px;top:14px;display:flex;align-items:center;gap:8px}
.follow i{width:24px;height:24px;border-radius:50%;border:1px solid var(--white);display:flex;align-items:center;justify-content:center}
.follow i::after{content:"";width:8px;height:8px;background:var(--white);border-radius:50%}
.copyright{right:162px;top:18px}
</style>
</head>
<body>

<div class="topbar">
  <div class="abs addr">
    <svg width="10" height="14" viewBox="0 0 10 14"><path d="M5 0a5 5 0 0 0-5 5c0 4 5 9 5 9s5-5 5-9a5 5 0 0 0-5-5zm0 7a2 2 0 1 1 0-4 2 2 0 0 1 0 4z" fill="#fff"/></svg>
    27 Harlow Crescent, Petone, Wellington
  </div>
  <div class="abs social"><span><i></i></span><span><i></i></span><span><i></i></span><span><i></i></span></div>
</div>

<header>
  <div class="abs brand"><span class="dot"></span>BRAMBLE WORKS</div>
  <nav class="abs nav"><span class="on">HOME</span><span>ABOUT US</span><span>SERVICES</span><span>TESTIMONIALS</span><span>CONTACT US</span></nav>
  <div class="abs callus">Any Query? Call us now
    <div class="num"><svg width="18" height="18" viewBox="0 0 24 24"><path d="M6.6 10.8a15 15 0 0 0 6.6 6.6l2.2-2.2c.3-.3.7-.4 1-.2 1.1.4 2.3.6 3.6.6.6 0 1 .4 1 1V20c0 .6-.4 1-1 1A17 17 0 0 1 3 4c0-.6.4-1 1-1h3.5c.6 0 1 .4 1 1 0 1.3.2 2.5.6 3.6.1.3 0 .7-.2 1z" fill="#33a6d7"/></svg>0 21 463 9027</div>
  </div>
</header>

<section class="hero">
  <div class="abs hero-photo" role="img" aria-label="Technician in hard hat and hi-vis vest fitting a ceiling cassette air conditioner"></div>
  <div class="abs hero-shade"></div>
  <div class="abs hero-copy">
    <h1>SPECIALIZING IN</h1>
    <p>Commercial And<br>Central Heating System</p>
    <div class="btns"><span class="btn btn-blue">Read More</span><span class="btn btn-orange">Contact Now</span></div>
  </div>
  <div class="abs dots"><i></i><i class="on"></i><i></i></div>
  <div class="abs hero-stripe"></div>
</section>

<section class="about">
  <h2 class="abs h-title"><span class="ring"></span>ABOUT <b>KELVAROOM</b></h2>
  <div class="abs sub">SPECIALIZING IN Commercial And Central Heating System</div>
  <p class="abs lead">Lorem ipsum dolor sit amet, consectetuer adipiscing elit, sed diam nonummy nibh eui smod tincidunt ut laoreet doloronsectetuer adipiscing elit, sed diam nonummy nibh eui smod tincid unt ut laoreet dolore magna aliquam erat volutpat. Ut wisi enim ad minim veniam.</p>
  <ul class="abs ticks">
    <li><svg width="14" height="10" viewBox="0 0 14 10"><path d="M0 5h12M8 1l4 4-4 4" stroke="#33a6d7" stroke-width="1.6" fill="none"/></svg>Lorem ipsum dolor sit amet, consectetur adipiscing elit.</li>
    <li><svg width="14" height="10" viewBox="0 0 14 10"><path d="M0 5h12M8 1l4 4-4 4" stroke="#33a6d7" stroke-width="1.6" fill="none"/></svg>Aenean luctus odio congue congue viverra.</li>
    <li><svg width="14" height="10" viewBox="0 0 14 10"><path d="M0 5h12M8 1l4 4-4 4" stroke="#33a6d7" stroke-width="1.6" fill="none"/></svg>Curabitur tempor magna sed arcu finibus, sed interdum risus hendrerit.</li>
    <li><svg width="14" height="10" viewBox="0 0 14 10"><path d="M0 5h12M8 1l4 4-4 4" stroke="#33a6d7" stroke-width="1.6" fill="none"/></svg>Maecenas vulputate elit eleifend tristique pharetra.</li>
    <li><svg width="14" height="10" viewBox="0 0 14 10"><path d="M0 5h12M8 1l4 4-4 4" stroke="#33a6d7" stroke-width="1.6" fill="none"/></svg>Mauris in ante quis tellus pulvinar dignissim.</li>
  </ul>
  <div class="abs btns"><span class="btn btn-blue">Read More</span><span class="btn btn-orange">Contact Now</span></div>
  <div class="abs about-photo" role="img" aria-label="Loft-style living room with exposed ceiling beams, brick wall and teal sofa"></div>
</section>

<section class="services">
  <h2 class="abs h-title"><span class="ring"></span>OUR <b>SERVICES</b></h2>
  <p class="abs intro">Heatpumps/Air Conditioning – Heat pumps are the most efficient way of using electricity to heat your home, but some are more efficient than others. We will select the right model for your requirements taking into account the capacity required, the visual impact of the system, the style of system, air flow and obviously your personal preferences. We only install the highest quality brands that offer outstanding after sales support. Cassettes, Consoles, Under Ceilings, Ducted, Hiwalls, Multis…</p>

  <div class="abs svc" style="left:204px">
    <svg width="242" height="358" viewBox="0 0 242 358"><polygon points="1,140 60,66 182,66 241,140 241,357 1,357" fill="none" stroke="#fff" stroke-width="1.5"/><circle cx="121" cy="76" r="74" fill="#fff"/><circle cx="121" cy="76" r="64" fill="none" stroke="#33a6d7" stroke-width="3"/>
      <rect x="93" y="62" width="56" height="20" rx="3" fill="none" stroke="#33a6d7" stroke-width="3"/><path d="M101 76h40M106 90l-4 10M121 90v12M136 90l4 10" stroke="#33a6d7" stroke-width="3" fill="none"/></svg>
    <h3>COMMERCIAL</h3>
    <p>We have a growing Portfolio of clients that rely on us for their Commercial requirements. We have proven ourselves to be a force to be reckoned with to be able...</p>
    <span class="btn btn-orange">Read More</span>
  </div>

  <div class="abs svc" style="left:483px">
    <svg width="242" height="358" viewBox="0 0 242 358"><polygon points="1,140 60,66 182,66 241,140 241,357 1,357" fill="none" stroke="#fff" stroke-width="1.5"/><circle cx="121" cy="76" r="74" fill="#fff"/><circle cx="121" cy="76" r="64" fill="none" stroke="#33a6d7" stroke-width="3"/>
      <path d="M97 58h48M97 98h48" stroke="#33a6d7" stroke-width="3"/><path d="M102 62v32M110 62v32M118 62v32M126 62v32M134 62v32M142 62v32" stroke="#33a6d7" stroke-width="4" stroke-linecap="round"/></svg>
    <h3>CENTRAL HEATING</h3>
    <p>Ducted Heatpumps are the holy grail of central heating and guess what? They can also cool and dehumidify your home. Ducted Heatpumps are often overlooked...</p>
    <span class="btn btn-orange">Read More</span>
  </div>

  <div class="abs svc" style="left:761px">
    <svg width="242" height="358" viewBox="0 0 242 358"><polygon points="1,140 60,66 182,66 241,140 241,357 1,357" fill="none" stroke="#fff" stroke-width="1.5"/><circle cx="121" cy="76" r="74" fill="#fff"/><circle cx="121" cy="76" r="64" fill="none" stroke="#33a6d7" stroke-width="3"/>
      <g fill="#33a6d7"><circle cx="121" cy="76" r="6"/><path d="M121 70c-4-10-2-20 6-22 6 6 2 16-6 22z"/><path d="M126 80c10 2 16 10 12 18-8 0-12-10-12-18z"/><path d="M116 80c-6 8-16 10-20 4 4-8 14-8 20-4z"/></g></svg>
    <h3>VENTILATION</h3>
    <p>Home ventilation is a very important part of insuring you have a nice dry home to maximise the efficiency of your Heat pump. Whilst HRV systems are not designed...</p>
    <span class="btn btn-orange">Read More</span>
  </div>

  <div class="abs cta">CONFUSED? GIVE US A CALL - 021 463 9027</div>
</section>

<section class="why">
  <h2 class="abs h-title"><span class="ring"></span>WHY CHOOSE <b>BRAMBLE WORKS</b></h2>
  <div class="abs feature" style="left:170px">
    <div class="art" role="img" aria-label="Isometric certificate box illustration"><i style="background:#2b2b2b"></i></div>
    <h4>EXPERIENCE<br>COUNTS</h4>
    <p>We have a team of nationally<br>trained and qualified. [+]</p>
  </div>
  <div class="abs feature" style="left:458px">
    <div class="art" role="img" aria-label="Shield guarantee illustration"><i style="background:#f5a417"></i></div>
    <h4>SATISFACTION<br>GUARANTEE</h4>
    <p>We aim to please and I put my name<br>behind our brand! [+]</p>
  </div>
  <div class="abs feature" style="left:750px">
    <div class="art" role="img" aria-label="Snowflake with warm air illustration"><i style="background:#2b2b2b"></i></div>
    <h4>LOW PRESSURE<br>SALES</h4>
    <p>We aim to please and I put my name<br>behind our brand! [+]</p>
  </div>
</section>

<section class="areas">
  <h2 class="abs h-title"><span class="ring"></span>AREAS WE <b>SERVICED</b></h2>
  <div class="abs loc">
    <svg width="14" height="20" viewBox="0 0 10 14"><path d="M5 0a5 5 0 0 0-5 5c0 4 5 9 5 9s5-5 5-9a5 5 0 0 0-5-5zm0 7a2 2 0 1 1 0-4 2 2 0 0 1 0 4z" fill="#666"/></svg>
    <div><div class="name">WELLINGTON</div><div class="street">27 Harlow Crescent, Petone, Wellington</div></div>
  </div>
  <div class="abs rule"></div>
  <p class="abs list">Wellington, Masterton,<br>Palmerston North, Wanganui and<br>anywhere in between.</p>
  <div class="abs areas-map" role="img" aria-label="Outline map of the lower North Island with the Wellington region highlighted"></div>
  <div class="abs map-tag">WELLINGTON</div>
</section>

<section class="testimonials">
  <h2 class="abs h-title"><span class="ring"></span>CLIENTS <b>TESTIMONIALS</b></h2>
  <div class="abs quote" style="left:162px">
    <p>Lorem ipsum dolor sit amet, consectetuer adipiscing elit, sed diam nonummy nibh euismod tincidunt ut laoreet dolore .</p>
    <div class="who"><div class="avatar" role="img" aria-label="Client portrait"></div><div><b>Tamsin Orle</b><span>Lorem Ipsum</span></div></div>
  </div>
  <div class="abs quote" style="left:462px">
    <p>Lorem ipsum dolor sit amet, consectetuer adipiscing elit, sed diam nonummy nibh euismod tincidunt ut laoreet dolore .</p>
    <div class="who"><div class="avatar" role="img" aria-label="Client portrait"></div><div><b class="hl">Tamsin Orle</b><span>Lorem Ipsum</span></div></div>
  </div>
  <div class="abs quote" style="left:761px">
    <p>Lorem ipsum dolor sit amet, consectetuer adipiscing elit, sed diam nonummy nibh euismod tincidunt ut laoreet dolore .</p>
    <div class="who"><div class="avatar" role="img" aria-label="Client portrait"></div><div><b>Tamsin Orle</b><span>Lorem Ipsum</span></div></div>
  </div>
</section>

<section class="contact">
  <div class="abs title"><span class="ring"></span><div>QUICK<br><b>CONTACT</b></div></div>
  <p class="abs blurb">Duis autem vel eum iriure dolormi opl inmokl mort hendi rerit in vulpu tatemi velitm essemol monop molestiel consequ ua.</p>
  <div class="abs ask">Please fill up bellow form</div>
  <div class="abs field" style="left:477px;top:70px">Name</div>
  <div class="abs field" style="left:770px;top:70px">Email</div>
  <div class="abs field" style="left:477px;top:114px">Phone</div>
  <div class="abs field" style="left:770px;top:114px">Message</div>
  <span class="abs btn btn-blue">Read More</span>
</section>

<footer>
  <div class="abs qlinks"><h5>QUICK <b>LINKS</b></h5>
    <ul><li>Home</li><li>About Us</li><li>Services</li><li>Testimonials</li><li>Contact Us</li></ul></div>
  <div class="abs cinfo"><h5>CONTACT <b>INFO</b></h5>
    <div class="row"><svg width="12" height="17" viewBox="0 0 10 14"><path d="M5 0a5 5 0 0 0-5 5c0 4 5 9 5 9s5-5 5-9a5 5 0 0 0-5-5zm0 7a2 2 0 1 1 0-4 2 2 0 0 1 0 4z" fill="#fff"/></svg><div>KELVAROOM<br>27 Harlow Crescent, Petone,<br>Wellington</div></div>
    <div class="row"><svg width="12" height="14" viewBox="0 0 24 24"><path d="M6.6 10.8a15 15 0 0 0 6.6 6.6l2.2-2.2c.3-.3.7-.4 1-.2 1.1.4 2.3.6 3.6.6.6 0 1 .4 1 1V20c0 .6-.4 1-1 1A17 17 0 0 1 3 4c0-.6.4-1 1-1h3.5c.6 0 1 .4 1 1 0 1.3.2 2.5.6 3.6.1.3 0 .7-.2 1z" fill="#fff"/></svg><div>021 463 9027</div></div>
    <div class="row"><svg width="14" height="12" viewBox="0 0 14 10"><rect x="0" y="0" width="14" height="10" fill="#fff"/><path d="M0 0l7 5 7-5" stroke="#050505" fill="none"/></svg><div>Marta.k@bramwks.co.nz</div></div>
  </div>
  <div class="abs fmap" role="img" aria-label="Street map of Petone with location pin"></div>
  <div class="abs fmap-link">View Map</div>
</footer>

<div class="bottombar">
  <div class="abs follow">Follow Us <i></i><i></i><i></i><i></i></div>
  <div class="abs copyright">Copyright © 2016 Northvale Studio. All Rights Reserved</div>
</div>

</body>
</html>
```